Business card design for new eCommerce site focusing on integrity and strong businsess tactics

We need a business card that will stand out and be memorable. Something with color that matches our company logo colors. Think high end version of Pactivo. There are 2 logos provided. The parent company is called Amber Ledge Partners and we are presenting a new and very exciting eCommerce site called BrightHarborTrade.example.

Target Market(s)

Our target markets are in the Activities, Food and Beverage, Health and Beauty

Industry/Entity Type

Marketing

Contact Information for Business Card

We have 4 members that need cards...I will provide all info to the winner of the design contest
Business Address is
4870 West 63rd Avenue, Suite C207
Phoenix AZ 85731

Font styles to use
Serif
Sans Serif

Colors

Designer to choose colors to be used in the design.

Requirements
Must have
• The card must be memorable...should be unique in design but must exude integrity and be playful .
• I have provided several colors or our parent company...please feel free to use which ever
Nice to have
• I will leave this up to you. Feel free to use other images of your choosing that wraps around our client.....Activities, Dining, Health, Beauty
Should not have
• just dont be boring

```html
<!DOCTYPE html>
<html lang="en">
<head>
<meta charset="utf-8">
<title>BrightHarborTrade.example business card</title>
<link rel="stylesheet" href="https://fonts.googleapis.com/css2?family=Open+Sans:wght@300;400;600;700&display=swap">
<style>
  :root {
    --backdrop: #2b2b2b;
    --brand-blue: #2a79a9;
    --paper: #f1f1f0;
    --ink-white: #ffffff;
    --ink-grey: #555a5e;
    --brand-green: #7dbb3c;
  }
  * { margin: 0; padding: 0; box-sizing: border-box; }
  html, body {
    width: 1200px;
    height: 960px;
    overflow: hidden;
    background: var(--backdrop);
    font-family: "Open Sans", Arial, sans-serif;
  }
  .stage { position: relative; width: 1200px; height: 960px; }

  .card {
    position: absolute;
    width: 600px;
    height: 343px;
    overflow: hidden;
    box-shadow: 0 2px 6px rgba(0,0,0,.45);
  }
  .card--front { left: 314px; top: 113px; background: var(--paper); }
  .card--back  { left: 311px; top: 472px; background: var(--brand-blue); }

  .front-panel { position: absolute; inset: 0; }

  .holder { position: absolute; left: 30px; top: 34px; color: var(--ink-white); }
  .holder__name { font-size: 21px; font-weight: 600; line-height: 1.1; letter-spacing: -0.2px; }
  .holder__title { font-size: 15px; font-weight: 300; margin-top: 3px; }

  .address {
    position: absolute; left: 30px; top: 170px;
    color: var(--ink-white); font-size: 14.5px; font-weight: 300; line-height: 18px;
  }

  .contacts {
    position: absolute; left: 30px; top: 236px; list-style: none;
    color: var(--ink-white); font-size: 14.5px; font-weight: 300; line-height: 19.5px;
  }
  .contacts li { display: flex; align-items: center; gap: 8px; }
  .contacts svg { width: 13px; height: 13px; fill: var(--ink-white); flex: none; }

  .brand {
    position: absolute; left: 352px; top: 182px; width: 240px; text-align: center;
  }
  .brand__name {
    font-size: 17.5px; font-weight: 600; color: var(--brand-blue); letter-spacing: -0.3px;
  }
  .brand__tagline {
    font-size: 10.5px; font-weight: 400; color: var(--ink-grey); letter-spacing: 0.9px; margin-top: 1px;
  }
  .brand__dot {
    display: block; width: 14px; height: 14px; border-radius: 50%;
    background: var(--brand-green); margin: 0 auto 8px;
  }

  .parent-mark {
    position: absolute; left: 228px; top: 71px; width: 146px; height: 146px;
    border-radius: 50%; background: var(--ink-white);
    box-shadow: 0 0 0 3px var(--brand-blue) inset, 0 0 0 6px var(--ink-white) inset;
  }
  .parent-name {
    position: absolute; left: 0; right: 0; top: 220px; text-align: center;
    color: var(--ink-white); font-size: 34px; font-weight: 700; letter-spacing: -0.3px;
  }
</style>
</head>
<body>
<main class="stage">

  <section class="card card--front" aria-label="Business card front">
    <svg class="front-panel" viewBox="0 0 600 343" preserveAspectRatio="none" aria-hidden="true">
      <path d="M0 0 H236 C 232 130, 300 270, 452 343 H0 Z" fill="var(--brand-blue)"/>
    </svg>

    <div class="holder">
      <p class="holder__name">Marcus Reed</p>
      <p class="holder__title">CEO/Founder</p>
    </div>

    <address class="address" style="font-style:normal">
      4870 West 63rd Avenue<br>
      Suite C207<br>
      Phoenix AZ 85731
    </address>

    <ul class="contacts">
      <li>
        <svg viewBox="0 0 16 16" aria-hidden="true"><path d="M3.6 1.2l2.3 2.6-1.3 1.9c.9 2 2.5 3.6 4.5 4.6l1.9-1.3 2.6 2.3-1.3 2.6C7 13.5 2.5 9 1 3.1z"/></svg>
        555 214 0387
      </li>
      <li>
        <svg viewBox="0 0 16 16" aria-hidden="true"><path d="M4.5 0h7a1.2 1.2 0 0 1 1.2 1.2v13.6A1.2 1.2 0 0 1 11.5 16h-7a1.2 1.2 0 0 1-1.2-1.2V1.2A1.2 1.2 0 0 1 4.5 0zm.6 2v10.5h5.8V2zM8 13.3a.9.9 0 1 0 0 1.8.9.9 0 0 0 0-1.8z"/></svg>
        555 903 6172
      </li>
      <li>
        <svg viewBox="0 0 16 16" aria-hidden="true"><path d="M1 3.5h14v9H1zm1.4 1L8 8.6l5.6-4.1z"/></svg>
        marcus@brightharbortrade.example
      </li>
      <li>
        <svg viewBox="0 0 16 16" aria-hidden="true"><path d="M8 1a7 7 0 1 0 0 14A7 7 0 0 0 8 1zm-1 2.2c-.6.8-2 1.2-2.2 2.4.6.7 1.8.4 2.2 1.3.3.7-.4 1.6.3 2.4.5.6.2 1.9.8 2.6-2.5-.2-4.4-2.3-4.4-4.9 0-1.6.8-3 2-3.9zm2.4.1A5 5 0 0 1 13 8c-.6.1-1.3-.4-1.8-1-.5-.7-1.4-.5-1.8-1.2-.3-.6.4-1.3 0-2.5z"/></svg>
        www.brightharbortrade.example
      </li>
    </ul>

    <div class="brand">
      <span class="brand__dot" aria-hidden="true"></span>
      <p class="brand__name">BrightHarborTrade.example</p>
      <p class="brand__tagline">Activities-Dining-Health-Beauty</p>
    </div>
  </section>

  <section class="card card--back" aria-label="Business card back">
    <span class="parent-mark" aria-hidden="true"></span>
    <p class="parent-name">Amber Ledge Partners</p>
  </section>

</main>
</body>
</html>
```